Thornbury Building Company - Card Design

I am looking to use the logo designs that you already did for me to develop a business card. I would like the card to have a black background and be double sided. I want white and green logo and text. I have attached an inspiration photo of a look that I like. I would like to use the Vertical Logo attached to take up the full front side of the card. On the back where I have my name and information, I would like to have the horizontal logo or maybe even just the image of the 'A' and trees without the text. I am open, but I am looking for something clean and simple and I want the green to really pop! Additional files can be found under Design #: 58302946

Target Market(s)

Homeowners

Industry/Entity Type

Construction

Contact Information for Business Card

Name: Marcus Thornbury, Title: Project Manager, Phone: 555.274.8136, Email: thornburybuildingcompany@mailvesta.com, address: 487 Larkspur Ln, Pinehollow, WA 95033, Lic# 2468317

Colors
00AB8E
00BBA5
67D7C9
C6EFE9
E9F9F6

Requirements
Nice to have
• I would like to see the logos that I have already got from ArtLoomHub, though I am open to new ones

```html
<!DOCTYPE html>
<html lang="en">
<head>
<meta charset="utf-8">
<title>Thornbury Building Company – Business Card</title>
<link href="https://fonts.googleapis.com/css2?family=Open+Sans:wght@400;600;700&display=swap" rel="stylesheet">
<style>
  :root {
    --backdrop: #4a4a4a;
    --card-black: #141414;
    --card-white: #ffffff;
    --green-deep: #3aa64a;
    --green-bright: #6db544;
    --text-dark: #222222;
    --text-light: #ffffff;
  }
  * { margin: 0; padding: 0; box-sizing: border-box; }
  html, body {
    width: 1200px; height: 801px; overflow: hidden;
    background: var(--backdrop);
    font-family: "Open Sans", Arial, sans-serif;
  }
  .canvas {
    position: relative; width: 1200px; height: 801px;
    display: flex; align-items: center; justify-content: center; gap: 40px;
  }
  .card {
    position: relative; width: 540px; height: 309px;
    overflow: hidden;
    box-shadow: 0 10px 30px rgba(0,0,0,.45);
    border-bottom: 3px solid var(--green-bright);
  }
  .card-art { position: absolute; inset: 0; width: 100%; height: 100%; }

  /* Contact side */
  .card-info { background: var(--card-white); }
  .brand-block {
    position: absolute; left: 30px; top: 104px; width: 170px;
    color: var(--text-light);
  }
  .brand-row { display: flex; align-items: center; gap: 10px; }
  .brand-dot {
    flex: none; width: 34px; height: 34px; border-radius: 50%;
    background: var(--green-bright);
  }
  .brand-name {
    font-weight: 700; font-size: 16px; line-height: 1.15;
    text-transform: uppercase; letter-spacing: .5px; color: var(--text-light);
  }
  .license { margin-top: 22px; font-size: 13px; color: var(--text-light); }

  .contact-block {
    position: absolute; right: 28px; top: 40px; text-align: right;
    color: var(--text-dark);
  }
  .person-name { font-weight: 700; font-size: 21px; color: var(--green-deep); }
  .person-title { font-size: 12.5px; margin-bottom: 16px; }
  .address { font-size: 12.5px; line-height: 1.45; margin-bottom: 16px; }
  .contact-line {
    display: flex; justify-content: flex-end; align-items: center; gap: 7px;
    font-size: 12px; line-height: 1.7;
  }
  .contact-icon { width: 11px; height: 11px; flex: none; }

  /* Logo side */
  .card-logo { background: var(--card-black); }
  .logo-lockup {
    position: absolute; inset: 0;
    display: flex; align-items: center; justify-content: center; gap: 16px;
  }
  .logo-dot {
    width: 46px; height: 46px; border-radius: 50%;
    background: var(--green-bright);
  }
  .logo-name {
    font-weight: 700; font-size: 26px; line-height: 1.15;
    text-transform: uppercase; letter-spacing: 1px; color: var(--text-light);
  }
</style>
</head>
<body>
<main class="canvas">

  <section class="card card-info" aria-label="Business card, contact side">
    <svg class="card-art" viewBox="0 0 540 309" preserveAspectRatio="none" aria-hidden="true">
      <path d="M0 0 H300 C250 70 234 215 160 309 H0 Z" fill="var(--green-bright)"/>
      <path d="M0 0 H288 C238 70 222 210 150 309 H0 Z" fill="var(--card-black)"/>
      <path d="M0 0 H278 C222 70 208 205 130 309 H0 Z" fill="var(--green-deep)"/>
      <path d="M0 0 H266 C208 70 196 200 110 309 H0 Z" fill="var(--card-black)"/>
    </svg>

    <div class="brand-block">
      <div class="brand-row">
        <span class="brand-dot"></span>
        <span class="brand-name">Thornbury Building Company</span>
      </div>
      <p class="license">License# 2468317</p>
    </div>

    <div class="contact-block">
      <h1 class="person-name">Marcus Thornbury</h1>
      <p class="person-title">Project Manager</p>
      <p class="address">487 Larkspur Ln,<br>Pinehollow, WA 95033</p>
      <p class="contact-line">555.274.8136
        <svg class="contact-icon" viewBox="0 0 24 24" aria-hidden="true"><path fill="var(--green-deep)" d="M6.6 10.8a15 15 0 0 0 6.6 6.6l2.2-2.2c.3-.3.7-.4 1-.2 1.1.4 2.3.6 3.6.6.6 0 1 .4 1 1V20c0 .6-.4 1-1 1A17 17 0 0 1 3 4c0-.6.4-1 1-1h3.5c.6 0 1 .4 1 1 0 1.3.2 2.5.6 3.6.1.3 0 .7-.2 1z"/></svg>
      </p>
      <p class="contact-line">thornburybuildingcompany@mailvesta.com
        <svg class="contact-icon" viewBox="0 0 24 24" aria-hidden="true"><path fill="var(--green-deep)" d="M2 5h20v14H2z"/><path fill="none" stroke="#fff" stroke-width="2" d="M2 5l10 8 10-8"/></svg>
      </p>
    </div>
  </section>

  <section class="card card-logo" aria-label="Business card, logo side">
    <div class="logo-lockup">
      <span class="logo-dot"></span>
      <span class="logo-name">Thornbury<br>Building Company</span>
    </div>
  </section>

</main>
</body>
</html>
```